Kelvo Marine Flyer Design Project

Hi we are a marine company based in Dubai. Im looking for a flyer which represents differant aspcts of of service lines... Velan-Torr Boats, Marine Parts, Sailing Clothes, New&Used boats.

All can be found on our Website .. www.kelvomarine.ae .. its basically taking our website info onto a flyer.

It Company

```html
<!DOCTYPE html>
<html lang="en">
<head>
<meta charset="utf-8">
<title>Kelvo Marine Flyer</title>
<link href="https://fonts.googleapis.com/css2?family=Open+Sans:wght@400;600;700&display=swap" rel="stylesheet">
<style>
  :root {
    --brand-red: #9b1b1f;
    --ink: #1c1c1c;
    --body-text: #4a4a4a;
    --paper: #ffffff;
    --paper-shade: #e9e9e9;
  }
  * { margin: 0; padding: 0; box-sizing: border-box; }
  html, body { width: 876px; height: 1200px; overflow: hidden; background: #fff; }
  body { font-family: "Open Sans", sans-serif; }
  .flyer {
    position: relative;
    width: 876px;
    height: 1200px;
    overflow: hidden;
    background: linear-gradient(160deg, var(--paper) 55%, var(--paper-shade) 100%);
  }
  .flyer__art { position: absolute; inset: 0; width: 876px; height: 1200px; }
  .brand-name {
    position: absolute; left: 59px; top: 834px;
    font-size: 46px; font-weight: 700; color: var(--ink);
    letter-spacing: 1px; line-height: 1;
  }
  .services { position: absolute; left: 506px; top: 723px; color: #fff; }
  .services__title { font-size: 18px; font-weight: 700; margin-bottom: 5px; }
  .services__list { list-style: none; font-size: 15.5px; }
  .services__list li { line-height: 28.3px; }
  .services__list li:nth-child(1) { margin-left: 15px; }
  .services__list li:nth-child(2) { margin-left: 28px; }
  .services__list li:nth-child(3) { margin-left: 41px; }
  .services__list li:nth-child(4) { margin-left: 53px; }
  .services__list li:nth-child(5) { margin-left: 66px; }
  .about { position: absolute; left: 59px; top: 914px; width: 478px; }
  .about__title { font-size: 15px; font-weight: 700; color: var(--brand-red); margin-bottom: 3px; }
  .about__text {
    font-size: 11.2px; line-height: 14.6px; color: var(--body-text);
    text-align: justify; margin-bottom: 10px;
  }
  .contact { position: absolute; left: 59px; top: 1143px; font-size: 13.5px; color: var(--body-text); }
  .contact__line { line-height: 24px; display: flex; align-items: center; gap: 6px; }
  .contact__name { color: var(--brand-red); }
  .contact__sep { margin: 0 6px; }
  .contact__icon { width: 12px; height: 12px; fill: var(--brand-red); }
  .contact__at { color: var(--brand-red); font-weight: 700; }
</style>
</head>
<body>
<main class="flyer">
  <svg class="flyer__art" viewBox="42 42 711 978" preserveAspectRatio="none">
    <defs>
      <radialGradient id="steelTone" cx="0.45" cy="0.45" r="0.75">
        <stop offset="0" stop-color="#e4e6e8"/>
        <stop offset="0.45" stop-color="#a9adb1"/>
        <stop offset="1" stop-color="#5f6366"/>
      </radialGradient>
      <linearGradient id="shoreTone" x1="0" y1="0" x2="0" y2="1">
        <stop offset="0" stop-color="#3e4a2c"/>
        <stop offset="0.45" stop-color="#6f7a55"/>
        <stop offset="0.7" stop-color="#b8b2a0"/>
        <stop offset="0.85" stop-color="#a8342c"/>
        <stop offset="1" stop-color="#8c8775"/>
      </linearGradient>
      <radialGradient id="seaTone" cx="0.72" cy="0.28" r="0.9">
        <stop offset="0" stop-color="#c9b79a"/>
        <stop offset="0.2" stop-color="#6f6a5a"/>
        <stop offset="0.45" stop-color="#2b5a50"/>
        <stop offset="0.75" stop-color="#1c3f37"/>
        <stop offset="1" stop-color="#a8b8b4"/>
      </radialGradient>
      <linearGradient id="seaWake" x1="0" y1="0" x2="1" y2="1">
        <stop offset="0.55" stop-color="#ffffff" stop-opacity="0"/>
        <stop offset="0.8" stop-color="#dfe9e6" stop-opacity="0.45"/>
        <stop offset="1" stop-color="#ffffff" stop-opacity="0"/>
      </linearGradient>
      <linearGradient id="blueTone" x1="0" y1="0" x2="0.6" y2="1">
        <stop offset="0" stop-color="#7ea4bf"/>
        <stop offset="0.35" stop-color="#4d6f88"/>
        <stop offset="0.55" stop-color="#b5703a"/>
        <stop offset="0.75" stop-color="#3f6a8a"/>
        <stop offset="1" stop-color="#dce8ef"/>
      </linearGradient>
      <radialGradient id="hullTone" cx="0.5" cy="0.4" r="0.7">
        <stop offset="0" stop-color="#8a5a32"/>
        <stop offset="0.35" stop-color="#4a3322"/>
        <stop offset="0.7" stop-color="#161616"/>
        <stop offset="1" stop-color="#050505"/>
      </radialGradient>
    </defs>

    <polygon role="img" aria-label="Photo of a chrome anchor windlass with chain on a boat deck"
      points="42,42 185,42 290,300 42,300" fill="url(#steelTone)"/>
    <polygon class="accent-stripe" points="200,42 210,42 287,258 279,258" fill="var(--brand-red)"/>
    <polygon class="accent-band" points="218,42 355,42 371,82 234,82" fill="var(--brand-red)"/>
    <polygon role="img" aria-label="Photo of a couple beside a red and white motorboat at the lakeshore"
      points="236,88 358,88 430,260 300,260" fill="url(#shoreTone)"/>
    <g role="img" aria-label="Photo of wooden-decked speedboats cruising on dark green water">
      <polygon points="362,42 753,42 753,765 628,522 520,262 447,262" fill="url(#seaTone)"/>
      <polygon points="362,42 753,42 753,765 628,522 520,262 447,262" fill="url(#seaWake)"/>
    </g>
    <polygon role="img" aria-label="Photo of a man driving a classic runabout across blue water"
      points="282,266 512,266 620,518 388,518" fill="url(#blueTone)"/>
    <polygon role="img" aria-label="Studio photo of a glossy black boat with a teak deck and small flag"
      points="66,308 272,308 420,612 226,612" fill="url(#hullTone)"/>
    <polygon class="service-band" points="392,523 612,523 753,792 753,1020 622,1020" fill="var(--brand-red)"/>
    <polygon class="accent-stripe" points="417,618 421,618 520,800 516,800" fill="var(--brand-red)"/>
  </svg>

  <div class="brand-name">Kelvo Marine</div>

  <section class="services">
    <h2 class="services__title">Services:</h2>
    <ul class="services__list">
      <li>Velan</li>
      <li>Torr Boats</li>
      <li>Marine Parts</li>
      <li>Sailing Clothes</li>
      <li>New &amp; Used boats</li>
    </ul>
  </section>

  <section class="about">
    <h2 class="about__title">About Us</h2>
    <p class="about__text">Kelvo Marine which is part of the “Kelvo Group” based out of Dubai (UAE) draws upon many years of marine experience, along with over 40 years of business acumen. Through their dealings with high worth individuals and blue chip organizations they are well placed too fully understand what’s required to launch a successful company and be able to offer high levels of service and support.</p>
    <p class="about__text">They are not looking at just being a brand that sells on numbers or price, they enjoy and are indeed passionate about the marine industry and want their company to represent not only that passion, but the quality and professionalism which has led the owners of Kelvo to be so successful in business over many years. Kelvo Marine will offer a high level brokerage service for luxury boats/yachts, supply marine spares and our launching an exciting new sailing clothing range called Tidewell sailing.</p>
  </section>

  <footer class="contact">
    <p class="contact__line"><span class="contact__name">Kelvo Marine</span><span class="contact__sep">I</span>Harbourline Business Park, Marsa Quay, Dubai, UAE</p>
    <p class="contact__line">
      <svg class="contact__icon" viewBox="0 0 12 12" aria-label="Phone"><path d="M2 1h2.5l1 3-1.5 1a7 7 0 0 0 3 3l1-1.5 3 1V11c-5 0-9-4-9-9z"/></svg>
      <span>971500000000</span>
      <span class="contact__at">@</span><span>info@kelvomarine.ae</span>
      <svg class="contact__icon" viewBox="0 0 12 12" aria-label="Website"><circle cx="6" cy="6" r="5.5"/><path d="M1 6h10M6 .5c2 2 2 9 0 11M6 .5c-2 2-2 9 0 11" stroke="#fff" stroke-width="1" fill="none"/></svg>
      <span>www.kelvomarine.ae</span>
    </p>
  </footer>
</main>
</body>
</html>
```